Tall Fern Roofing Business Card

Need a business card with the logo that was designed here

Contact Information for Business Card

Name, Title, Phone, Email, Website, Company name

```html
<!DOCTYPE html>
<html lang="en">
<head>
<meta charset="UTF-8">
<title>Tall Fern Roofing Business Card</title>
<link rel="stylesheet" href="https://fonts.googleapis.com/css2?family=Poppins:wght@400;700&display=swap">
<style>
  :root {
    --brand-blue: #2077c0;
    --card-white: #ffffff;
    --rule-grey: #9a9a9e;
    --backdrop: #2a2a2c;
  }
  html, body {
    margin: 0;
    width: 1200px;
    height: 1015px;
    overflow: hidden;
    background: var(--backdrop);
    font-family: "Poppins", sans-serif;
  }
  .stage {
    position: relative;
    width: 1200px;
    height: 1015px;
  }
  .card {
    position: absolute;
    left: 300px;
    width: 600px;
    height: 343px;
    overflow: hidden;
    box-shadow: 0 14px 30px rgba(0,0,0,0.55);
  }
  .card--front { top: 120px; background: var(--brand-blue); }
  .card--back  { top: 552px; background: var(--card-white); }

  .wordmark {
    position: absolute;
    display: flex;
    align-items: center;
    gap: 12px;
    font-weight: 700;
    font-size: 34px;
    letter-spacing: 0.5px;
    white-space: nowrap;
  }
  .wordmark__square {
    width: 22px;
    height: 22px;
    background: currentColor;
  }
  .card--front .wordmark {
    color: var(--card-white);
    left: 50%;
    top: 50%;
    transform: translate(-50%, -50%);
  }
  .card--back .wordmark {
    color: var(--brand-blue);
    right: 38px;
    top: 62px;
    font-size: 30px;
  }

  .back-bands {
    position: absolute;
    inset: 0;
  }
  .contact {
    position: absolute;
    left: 40px;
    bottom: 34px;
    color: var(--card-white);
  }
  .contact__name {
    margin: 0;
    font-weight: 700;
    font-size: 21px;
    letter-spacing: 0.5px;
    line-height: 1.1;
  }
  .contact__title {
    margin: 2px 0 22px;
    font-weight: 400;
    font-size: 16px;
  }
  .contact__list {
    list-style: none;
    margin: 0;
    padding: 0;
    font-size: 15px;
    line-height: 1.45;
  }
  .contact__list li {
    display: flex;
    align-items: center;
    gap: 9px;
  }
  .contact__icon {
    width: 15px;
    height: 15px;
    flex: none;
  }
</style>
</head>
<body>
<main class="stage">

  <section class="card card--front" aria-label="Card front">
    <div class="wordmark"><span class="wordmark__square"></span>Tall Fern Roofing</div>
  </section>

  <section class="card card--back" aria-label="Card back">
    <svg class="back-bands" viewBox="0 0 600 343" preserveAspectRatio="none" aria-hidden="true">
      <polygon points="0,0 96,0 518,343 0,343" fill="var(--brand-blue)"/>
      <line x1="105" y1="-3" x2="534" y2="346" stroke="var(--rule-grey)" stroke-width="4"/>
    </svg>

    <div class="wordmark"><span class="wordmark__square"></span>Tall Fern Roofing</div>

    <div class="contact">
      <h1 class="contact__name">MARCUS HALE</h1>
      <p class="contact__title">Managing Director</p>
      <ul class="contact__list">
        <li>
          <svg class="contact__icon" viewBox="0 0 16 16" aria-hidden="true"><path d="M3 1.5l3 3-1.6 1.8c.9 2 2.4 3.5 4.3 4.3L10.5 9l3 3-2 2.5C6 14 2 10 1.5 4.5z" fill="none" stroke="#fff" stroke-width="1.5" stroke-linejoin="round"/></svg>
          044-555 017 342
        </li>
        <li>
          <svg class="contact__icon" viewBox="0 0 16 16" aria-hidden="true"><rect x="1" y="3" width="14" height="10" fill="#fff"/><path d="M1 3l7 6 7-6" fill="none" stroke="var(--brand-blue)" stroke-width="1.4"/></svg>
          info@tallfernroofing.com
        </li>
        <li>
          <svg class="contact__icon" viewBox="0 0 16 16" aria-hidden="true"><g fill="none" stroke="#fff" stroke-width="1.3"><circle cx="8" cy="8" r="6.5"/><ellipse cx="8" cy="8" rx="3" ry="6.5"/><path d="M1.5 8h13M2.6 4.5h10.8M2.6 11.5h10.8"/></g></svg>
          www.tallfernroofing.com
        </li>
      </ul>
    </div>
  </section>

</main>
</body>
</html>
```